Sell the dream! Property investment proposal document

We are looking for a proposal document which outlines our vision for property development. The purpose of the document is to raise investment from investors - sell the dream!
Brief summary:
Kestrel Dwellings Developments, is an emerging New Zealand property investment company with a focus on providing unique property investment opportunities.
Our expertise and capabilities in architectural modular homes provide us with a remarkable advantage in tackling the development of properties that are typically considered challenging, remote, or uniquely positioned.
Our specialization in this niche sector of property development not only sets us apart from competitors, but also paves the way for lucrative investment opportunities in the New Zealand property market.
Feel free to use any images from www.kestreldwellings.co.nz
Target Market(s)
investors for a unique property development opportunity
Industry/Entity Type
luxury property development in unique locations throughout New Zealand
Colors
Designer to choose only greyscale colors for use in the design.
Look and feel

```html
<!DOCTYPE html>
<html lang="en">
<head>
<meta charset="utf-8">
<title>Kestrel Dwellings Developments – Investment Proposal</title>
<link href="https://fonts.googleapis.com/css2?family=Noto+Serif:wght@400;700&display=swap" rel="stylesheet">
<style>
  :root {
    --board: #2b2b2b;
    --ink: #262626;
    --body-ink: #5c5c5c;
    --paper: #ffffff;
    --paper-cool: #f7f8fa;
    --sky-top: #dfe9fb;
    --sky-bottom: #ffffff;
    --cover-green: #56633f;
    --cover-dark: #232421;
    --interior-warm: #a08d6c;
    --interior-grey: #8e8f8d;
    --hill-green: #6f9440;
    --house-dark: #3a3a38;
  }
  * { margin: 0; padding: 0; box-sizing: border-box; }
  html, body { width: 900px; height: 1200px; overflow: hidden; background: var(--board); }
  body { position: relative; font-family: "Noto Serif", Georgia, serif; color: var(--ink); }

  .page { position: absolute; width: 372px; height: 526px; overflow: hidden; }
  .page--cover { left: 56px; top: 50px; background: var(--paper-cool); }
  .page--origins { left: 472px; top: 50px; background: var(--paper); }
  .page--finance { left: 56px; top: 623px;
    background: linear-gradient(180deg, var(--sky-top) 0%, var(--sky-bottom) 58%); }

  /* Cover */
  .cover-photo { position: absolute; left: 0; top: 190px; width: 100%; height: 336px;
    background: linear-gradient(180deg, var(--paper-cool) 0%, #dfe1df 10%, var(--cover-green) 30%, var(--cover-green) 48%, var(--cover-dark) 52%, var(--cover-dark) 82%, #cfd0cd 88%, #d8d9d6 100%); }
  .cover-frame { position: absolute; left: 19px; top: 14px; width: 334px; height: 226px; }
  .cover-title { position: absolute; left: 0; width: 100%; top: 56px; text-align: center;
    font-size: 58px; font-weight: 400; line-height: 1; color: var(--ink); }
  .cover-intro { position: absolute; left: 45px; width: 282px; top: 128px; text-align: center;
    font-size: 8.2px; line-height: 15px; color: var(--ink); }
  .cover-ghost { position: absolute; left: 0; width: 100%; top: 198px; text-align: center;
    font-size: 84px; font-weight: 400; line-height: 1; color: rgba(255,255,255,0.3); }

  /* Body pages */
  .section-title { position: absolute; font-size: 12.5px; font-weight: 700; line-height: 1; color: var(--ink); }
  .body-copy { position: absolute; font-size: 5.5px; line-height: 13px; color: var(--body-ink); letter-spacing: -0.05px; }
  .body-copy p + p { margin-top: 13px; }

  .page--origins .section-title { left: 18px; top: 64px; }
  .page--origins .body-copy { left: 18px; top: 86px; width: 160px; }
  .origins-photo { position: absolute; left: 193px; top: 27px; width: 179px; height: 471px;
    background: linear-gradient(180deg, #4d4239 0%, #4d4239 11%, var(--interior-grey) 22%, var(--interior-warm) 40%, var(--interior-warm) 62%, #a7a8a5 76%, #6f6f6d 100%); }

  .page--finance .section-title { left: 23px; top: 25px; }
  .page--finance .body-copy { left: 23px; top: 45px; width: 332px; }
  .pull-quote { position: absolute; left: 45px; width: 282px; top: 228px; text-align: center;
    font-size: 11.5px; line-height: 18px; color: var(--ink); }
  .finance-photo { position: absolute; left: 0; top: 296px; width: 100%; height: 230px;
    background: linear-gradient(180deg, rgba(255,255,255,0) 0%, var(--house-dark) 6%, var(--house-dark) 30%, #7d8478 42%, var(--hill-green) 58%, var(--hill-green) 100%); }
</style>
</head>
<body>

<section class="page page--cover">
  <div class="cover-photo" role="img" aria-label="Black timber modular home set among trees with a misty hill behind and a paved path in front"></div>
  <div class="cover-ghost" aria-hidden="true">Kestrel</div>
  <svg class="cover-frame" viewBox="0 0 334 226" aria-hidden="true">
    <polyline points="1,213 1,1 333,1 333,226" fill="none" stroke="#262626" stroke-width="1.5"/>
  </svg>
  <h1 class="cover-title">Kestrel</h1>
  <p class="cover-intro">Kestrel homes can be delivered nationwide, to the most unique, and difficult to reach locations in New Zealand. Some of our most popular locations Include Waiheke Island, Mangawhai, Wellington, Martinborough, Great Barrier Island, Queenstown, and more.</p>
</section>

<section class="page page--origins">
  <h2 class="section-title">Business Origins</h2>
  <div class="body-copy">
    <p>Kestrel Dwellings Developments was established with the goal of transforming the property investment market in New Zealand by introducing an innovative approach that centers on architectural modular designs and streamlined project timelines.</p>
    <p>Driven by our enthusiasm for architecture and real estate, we have expanded our successful business model to not only offer financial opportunities for investors but also to expand on our passion for high-end architectural design.</p>
    <p>With a wealth of experience accumulated over the past six years in the construction and the property market, we are pivoting to focus solely on our property development initiatives, presenting completed Kestrel projects to the market, in exclusive locations.</p>
    <p>These projects will boast high-quality standards, meticulous attention to detail and landscaping, and creative design elements.</p>
    <p>By introducing completed Kestrel properties into the market, we aim to reach a wider audience, catering to individuals who prefer ready-to-occupy homes, over engaging in the design and construction process.</p>
    <p>This approach also simplifies the financing process for prospective buyers, as established properties are often preferred by financial lenders.</p>
  </div>
  <div class="origins-photo" role="img" aria-label="Glass-walled interior with a leather lounge chair on a hide rug, looking out to dry tussock hills"></div>
</section>

<section class="page page--finance">
  <h2 class="section-title">Financial Summary</h2>
  <div class="body-copy">
    <p>In terms of financial projections, with each development, we anticipate a profit of 10%-20% which will be project dependent.</p>
    <p>This growth is fueled by the increasing demand for unique property investments in New Zealand and our ability to deliver high-quality services to the market in a condensed time frame, with heavily controlled costs.</p>
    <p>With a solid business model and a dedicated team, we are confident in our ability to achieve success and establish Kestrel Dwellings Investments as a trusted name in the industry.</p>
    <p>New Zealand's property market has been experiencing steady growth over the years, making it an attractive destination for property investors. With its beautiful landscapes and strong economy, New Zealand offers a diverse range of investment opportunities for both local and international investors. The demand for quality properties in prime locations continues to rise, creating a favorable environment for property investment companies like ours that can lean on our modular benefits of being able to reach unique and remote locations.</p>
  </div>
  <p class="pull-quote">Kestrel’s processes ensure that clear communication about scheduling and costs is maintained at all times.</p>
  <div class="finance-photo" role="img" aria-label="Dark cantilevered modular home on a grassy hillside with rocks, overlooking a lake"></div>
</section>

</body>
</html>
```